Computer Company needs a Business card design

We need a business card design for our business. We assist people to transition to the KVS (Kestrel Vantage Scheme). The Verandal Crown Office-owned kvs™ network is a brand new telecommunications network currently being rolled out across Australia, giving access to a reliable broadband connection. Our niche market will predominantly be domestic customers in the 50+ age bracket. The assistance that we provide is everything from arranging the equipment, arranging the plan and contract term, appointment times, final testing of the network and any tweaks that need to be made. We basically PM the transition from start to finish. The business card design should be minimalist, should communicate loyalty and stability, should be easy to read and clearly explain what we do. We have asked for front and back. However, the back of the card does not have to include much information at all. It could be just a small design, or a repeat of our phone number. Up to you. The attached file only says what is required on the card. It does not specify where to arrange the text, what fonts to use, etc etc. As much as we would like to give you more info, due to our very limited design ability, we are not really able to send you any rough, or otherwise, designs of what we are after. Hopefully the above description is enough for you.

```html
<!DOCTYPE html>
<html lang="en">
<head>
<meta charset="utf-8">
<title>KVSME Business Card</title>
<link href="https://fonts.googleapis.com/css2?family=Roboto:wght@300;400;500;700&display=swap" rel="stylesheet">
<style>
  :root {
    --stage: #1f1f21;
    --card-grey: #5b5b5e;
    --card-white: #ffffff;
    --band-grey: #58585b;
    --blue-light: #1ba3e3;
    --blue-deep: #1571bd;
    --text-light: #ffffff;
    --text-soft: #e4e4e6;
  }
  html, body {
    margin: 0;
    padding: 0;
    width: 1200px;
    height: 900px;
    overflow: hidden;
    background: var(--stage);
    font-family: "Roboto", Arial, sans-serif;
  }
  .canvas {
    position: relative;
    width: 1200px;
    height: 900px;
  }
  .card {
    position: absolute;
    left: 300px;
    width: 600px;
    height: 343px;
    border-radius: 18px;
    overflow: hidden;
    box-shadow: 0 14px 30px rgba(0,0,0,0.45);
  }
  .card-back {
    top: 72px;
    background: var(--card-grey);
    display: flex;
    align-items: center;
    justify-content: center;
  }
  .card-front {
    top: 475px;
    background: var(--card-white);
  }
  .brand {
    display: flex;
    align-items: center;
    gap: 14px;
  }
  .brand-dot {
    width: 22px;
    height: 22px;
    border-radius: 50%;
    background: var(--blue-light);
  }
  .brand-name {
    font-weight: 700;
    font-size: 68px;
    letter-spacing: 2px;
    line-height: 1;
  }
  .card-back .brand-name { color: var(--text-light); }
  .card-front .brand {
    position: absolute;
    left: 62px;
    top: 118px;
  }
  .card-front .brand-name {
    color: var(--band-grey);
    font-size: 54px;
  }
  .card-front .brand-dot {
    width: 18px;
    height: 18px;
  }
  .wave {
    position: absolute;
    inset: 0;
  }
  .contact {
    position: absolute;
    right: 30px;
    top: 112px;
    text-align: right;
    color: var(--text-soft);
  }
  .contact-name {
    margin: 0;
    font-size: 24px;
    font-weight: 500;
    color: var(--text-light);
  }
  .contact-role {
    margin: 2px 0 12px;
    font-size: 14px;
    font-weight: 300;
  }
  .contact-list {
    list-style: none;
    margin: 0;
    padding: 0;
    font-size: 14px;
    font-weight: 300;
    line-height: 1.6;
  }
  .contact-list li {
    display: flex;
    align-items: center;
    justify-content: flex-end;
    gap: 10px;
  }
  .contact-icon {
    width: 12px;
    height: 12px;
    flex: none;
  }
</style>
</head>
<body>
<main class="canvas">

  <section class="card card-back" aria-label="Card back">
    <div class="brand">
      <span class="brand-dot"></span>
      <span class="brand-name">KVSME</span>
    </div>
  </section>

  <section class="card card-front" aria-label="Card front">
    <svg class="wave" viewBox="0 0 600 343" width="600" height="343" aria-hidden="true">
      <path d="M0 292 C170 298 300 270 345 190 C385 110 470 40 600 28 L600 343 L0 343 Z" fill="var(--band-grey)"/>
      <path d="M0 270 C170 280 290 250 335 175 C378 95 465 22 600 12" fill="none" stroke="var(--blue-light)" stroke-width="9"/>
      <path d="M120 262 C240 256 300 230 328 170 C370 80 460 10 600 -2" fill="none" stroke="var(--blue-deep)" stroke-width="6"/>
    </svg>

    <div class="brand">
      <span class="brand-dot"></span>
      <span class="brand-name">KVSME</span>
    </div>

    <div class="contact">
      <h2 class="contact-name">Dale Merrow</h2>
      <p class="contact-role">Director</p>
      <ul class="contact-list">
        <li>0491570156
          <svg class="contact-icon" viewBox="0 0 12 12" aria-hidden="true"><path d="M2.5 1 L4.5 1 L5.3 3.5 L4 4.5 C4.6 6 6 7.4 7.5 8 L8.5 6.7 L11 7.5 L11 9.5 C11 10.3 10.3 11 9.5 11 C5 11 1 7 1 2.5 C1 1.7 1.7 1 2.5 1 Z" fill="currentColor"/></svg>
        </li>
        <li>info@kvsmadeeasy.com.au
          <svg class="contact-icon" viewBox="0 0 12 12" aria-hidden="true"><rect x="1" y="2.5" width="10" height="7" fill="none" stroke="currentColor" stroke-width="1.2"/><path d="M1 2.5 L6 6.5 L11 2.5" fill="none" stroke="currentColor" stroke-width="1.2"/></svg>
        </li>
        <li>www.kvsmadeeasy.com.au
          <svg class="contact-icon" viewBox="0 0 12 12" aria-hidden="true"><circle cx="6" cy="6" r="5" fill="none" stroke="currentColor" stroke-width="1.2"/><path d="M1 6 H11 M6 1 C3.5 3.5 3.5 8.5 6 11 M6 1 C8.5 3.5 8.5 8.5 6 11" fill="none" stroke="currentColor" stroke-width="1"/></svg>
        </li>
      </ul>
    </div>
  </section>

</main>
</body>
</html>
```